New Business Card Design Project

Need a design that will create an impact / strong impression towards our clients for our business. We are in the lighting business and we do lighting retrofits for large commercial to industrial clientele.

Target Market(s)

Lighting Industry

Industry/Entity Type

Business

Font styles to use
Other font styles liked:
• we would like to use the font on our logo, not sure what it is though..

Requirements
Must have
• Our logo.
Nice to have
• We are open to suggestions that have to do with lighting.

```html
<!DOCTYPE html>
<html lang="en">
<head>
<meta charset="utf-8">
<title>Lumenvale Retrofit Co. – Business Card</title>
<link rel="stylesheet" href="https://fonts.googleapis.com/css2?family=Montserrat:wght@400;500;700;800&display=swap">
<style>
  :root {
    --bg: #2b2b2b;
    --green-bright: #14c257;
    --green-mid: #0c8f3e;
    --green-deep: #0b6a2e;
    --green-dark: #0a5a26;
    --green-light: #66c45a;
    --logo-green: #1f7a3a;
    --white: #ffffff;
    --ink: #1d4a2a;
  }
  * { margin: 0; padding: 0; box-sizing: border-box; }
  html, body { width: 1200px; height: 900px; overflow: hidden; }
  body {
    background: var(--bg);
    font-family: "Montserrat", Arial, sans-serif;
    position: relative;
  }
  .card {
    position: absolute;
    width: 620px;
    height: 354px;
    overflow: hidden;
    box-shadow: 0 18px 40px rgba(0,0,0,0.45);
  }

  /* Front */
  .card-front {
    left: 110px; top: 90px;
    background: linear-gradient(120deg, var(--green-bright) 0%, var(--green-mid) 55%, var(--green-deep) 100%);
    color: var(--white);
  }
  .front-brand {
    position: absolute; left: 0; right: 0; top: 112px;
    text-align: center;
  }
  .brand-name {
    display: inline-flex; align-items: center; gap: 12px;
    font-weight: 800; font-size: 40px; letter-spacing: 1px;
  }
  .brand-square {
    width: 22px; height: 22px; background: currentColor; display: inline-block;
  }
  .brand-rule {
    width: 300px; height: 1px; background: currentColor; margin: 10px auto 6px; opacity: .9;
  }
  .brand-tag {
    font-size: 11px; font-weight: 700; letter-spacing: 1.5px; text-transform: uppercase;
  }
  .front-web {
    position: absolute; left: 0; right: 0; bottom: 36px;
    text-align: center; font-size: 13px; letter-spacing: 2.5px; font-weight: 500;
  }

  /* Back */
  .card-back {
    left: 470px; top: 430px;
    background: var(--white);
  }
  .back-shapes { position: absolute; inset: 0; }
  .person {
    position: absolute; left: 28px; top: 66px; color: var(--white);
  }
  .person-name { font-weight: 800; font-size: 19px; letter-spacing: .5px; text-transform: uppercase; }
  .person-role { font-weight: 400; font-size: 14px; margin-top: 2px; text-transform: uppercase; }
  .contact {
    position: absolute; left: 28px; top: 196px; color: var(--white);
    font-size: 13px; line-height: 17px;
  }
  .address { margin-bottom: 4px; }
  .contact-list { list-style: none; }
  .contact-list li { display: flex; align-items: center; gap: 10px; }
  .contact-list svg { width: 12px; height: 12px; flex: none; }
  .back-brand {
    position: absolute; left: 300px; width: 300px; top: 126px;
    text-align: center; color: var(--logo-green);
  }
  .back-brand .brand-name { font-size: 30px; gap: 10px; }
  .back-brand .brand-square { width: 16px; height: 16px; }
  .back-brand .brand-rule { width: 230px; }
  .back-brand .brand-tag { font-size: 9px; color: var(--ink); }
</style>
</head>
<body>

<section class="card card-front" aria-label="Card front">
  <div class="front-brand">
    <div class="brand-name"><span>LUMENVALE</span><span class="brand-square"></span></div>
    <div class="brand-rule"></div>
    <div class="brand-tag">Lumenvale Retrofit Co.</div>
  </div>
  <div class="front-web">www.lumenvaleretrofit.com</div>
</section>

<section class="card card-back" aria-label="Card back">
  <svg class="back-shapes" viewBox="0 0 620 354" width="620" height="354" aria-hidden="true">
    <polygon points="0,0 252,0 212,148 0,160" fill="var(--green-light)"/>
    <polygon points="0,168 216,156 500,354 0,354" fill="var(--green-deep)"/>
    <polygon points="216,156 500,354 420,354 180,200" fill="var(--green-dark)" opacity=".35"/>
  </svg>

  <div class="person">
    <div class="person-name">Daniel Reyes</div>
    <div class="person-role">CEO/Founder</div>
  </div>

  <div class="contact">
    <div class="address">2140 Cedar Ridge Road<br>Fernhollow<br>Nevada 89517</div>
    <ul class="contact-list">
      <li>
        <svg viewBox="0 0 12 12"><path d="M2 1h3l1 3-1.5 1a6 6 0 0 0 2.5 2.5L8 6l3 1v3a1 1 0 0 1-1 1A9 9 0 0 1 1 2a1 1 0 0 1 1-1z" fill="currentColor"/></svg>
        555 214 7730
      </li>
      <li>
        <svg viewBox="0 0 12 12"><rect x="3" y="0.5" width="6" height="11" rx="1" fill="none" stroke="currentColor"/><circle cx="6" cy="9.5" r=".7" fill="currentColor"/></svg>
        555 390 1186
      </li>
      <li>
        <svg viewBox="0 0 12 12"><rect x="1" y="4" width="10" height="6" fill="currentColor"/><rect x="3" y="1" width="6" height="3" fill="none" stroke="currentColor"/></svg>
        555 672 4059
      </li>
      <li>
        <svg viewBox="0 0 12 12"><rect x="0.5" y="2.5" width="11" height="7" fill="currentColor"/><path d="M0.5 2.5 6 7l5.5-4.5" fill="none" stroke="var(--green-deep)"/></svg>
        hello@lumenvaleretrofit.com
      </li>
      <li>
        <svg viewBox="0 0 12 12"><circle cx="6" cy="6" r="5" fill="none" stroke="currentColor"/><path d="M1 6h10M6 1c-2 2.5-2 7.5 0 10M6 1c2 2.5 2 7.5 0 10" fill="none" stroke="currentColor" stroke-width=".8"/></svg>
        www.lumenvaleretrofit.com
      </li>
    </ul>
  </div>

  <div class="back-brand">
    <div class="brand-name"><span>LUMENVALE</span><span class="brand-square"></span></div>
    <div class="brand-rule"></div>
    <div class="brand-tag">Lumenvale Retrofit Co.</div>
  </div>
</section>

</body>
</html>
```